Revise Three Graphics for Company Careers website.

We have a need to find an alternative artistic approach to revising three graphics currently used on a growing companies careers/job website.
- The new art for attached graphics (named graphic #1, #2, and #3) should be clean, professional and easy to read.
- The art representing these three pieces should share common artistic elements and not necessarily look like three differently branded pieces.
- The careers site is shared between two related companies, so the colors used should complement the colors of two companies (whose logos are attached).
- Logos can be used as knock-outs if needed.
Note: Graphic #3 (currently a set of boxes 2x3) needs two additional boxes with the following copy:
- Art and Science of Communication
- Supervising 101
Lastly, Graphic #4 we need to be put into the same color font used in the two company logos. That's it!

```html
<!DOCTYPE html>
<html lang="en">
<head>
<meta charset="utf-8">
<title>Learning and Development Programs</title>
<link rel="stylesheet" href="https://fonts.googleapis.com/css2?family=Open+Sans:wght@400;600&display=swap">
<style>
  :root {
    --page-light: #ffffff;
    --page-mid: #f1f1f2;
    --page-edge: #d9d9db;
    --frame: #9a9a9c;
    --navy: #154e8a;
    --teal-ring: #3aacbd;
    --red: #f01f38;
    --green: #9ccc00;
    --sky: #48c9e3;
    --ink-navy: #1d3c6e;
    --ink-grey: #585858;
    --ink-dark: #222222;
    --white: #ffffff;
  }
  html, body {
    margin: 0;
    padding: 0;
    overflow: hidden;
  }
  .canvas {
    position: relative;
    width: 849px;
    height: 1200px;
    box-sizing: border-box;
    border-left: 1px solid var(--frame);
    border-top: 1px solid var(--frame);
    background: radial-gradient(ellipse at 50% 55%, var(--page-light) 0%, var(--page-mid) 60%, var(--page-edge) 100%);
    font-family: "Open Sans", sans-serif;
    overflow: hidden;
  }
  .program {
    position: absolute;
    width: 206px;
    height: 206px;
    margin: -103px 0 0 -103px;
    border-radius: 50%;
    box-sizing: border-box;
    display: flex;
    align-items: center;
    justify-content: center;
    text-align: center;
    padding: 0 18px;
    font-size: 20.5px;
    line-height: 1.45;
    box-shadow: 0 4px 10px rgba(0, 0, 0, 0.28);
  }
  .program--filled {
    color: var(--white);
    font-weight: 600;
    letter-spacing: -0.3px;
  }
  .program--outlined {
    background: var(--white);
    border: 5px solid var(--teal-ring);
    font-weight: 400;
  }
  .program--navy { background: var(--navy); }
  .program--red { background: var(--red); }
  .program--green { background: var(--green); }
  .program--sky { background: var(--sky); }
  .ink-navy { color: var(--ink-navy); }
  .ink-grey { color: var(--ink-grey); }
  .ink-dark { color: var(--ink-dark); }
  .col-left { left: 309px; }
  .col-right { left: 532px; }
  .row-1 { top: 264px; }
  .row-2 { top: 480px; }
  .row-3 { top: 701px; }
  .row-4 { top: 922px; }
</style>
</head>
<body>
<main class="canvas">
  <div class="program program--filled program--navy col-left row-1">Scientific Lunch and Learns</div>
  <div class="program program--outlined ink-navy col-right row-1">Statistics in Pharmaceutical Development Workshop</div>
  <div class="program program--outlined ink-navy col-left row-2">Conferences and Seminars</div>
  <div class="program program--filled program--red col-right row-2">Leadership Development</div>
  <div class="program program--filled program--green col-left row-3">Creating the Right Team Workshop</div>
  <div class="program program--outlined ink-grey col-right row-3">Project Management Training</div>
  <div class="program program--outlined ink-dark col-left row-4">Art and Science of Communication</div>
  <div class="program program--filled program--sky col-right row-4">Supervising 101</div>
</main>
</body>
</html>
```